Business Card: RW Office Partners - Your organised problem solver

Business Name: RW Office Partners
Website: www.rwofficepartners.com.au
Email: marisol@rwofficepartners.com.au
Mobile: 61 482 907 236
Facebook: @rwofficepartners
Instrgram: @rwofficepartners

Brading Colours:
HEX
#986474
#ddccd3
#7a8498
#c9d8e4
#000000
#ffffff

Tag Line: Your organised problem solver

Link to DRAFT website:
https://deskhelpcollective.wixsite.com/rw-office-partners

About Page from the website:
My name is Marisol Wrenfield, and I would love to assist you to become more productive in your day to day and achieve your business and personal goals.
My mission is to give you time, time to work on the important tasks of your business or to be able to spend more time with your family. I will take on the tasks you don’t have time for, don’t know well or simply don’t like to do.
I have an extensive background in Administration, Tender Coordination, Document Control, WHS and Quality Management working primarily in the Construction, Mining and Corporate World.
I am passionate about being organised, having order and making things in your life (and mine) easier! I love to watch something unfold and grow into something amazing! I am known for being the go-to problem solver, the organiser of all things, producing high standards of work even under pressure. I’m also a confident communicator, and I understand that you’re busy running your business.

Target Market(s)

Small to Medium Business who require assistance in their business by a virtual assistant.

Industry/Entity Type

Virtual Assistant

Contact Information for Business Card

Mobile: 61 482 907 236

Font styles to use
Sans Serif

Colors
ffffff

Requirements
Must have
• Branding Colours as outlined.
Contact Details as outlined.
Logo as provided.
Proper contact details - mobile, facebook, instragm, website.
Simple, Elegant, very clean looking.
Should not have
• Note cute with pictures.
Not too girly as still want to market to construction companies.

```html
<!DOCTYPE html>
<html lang="en">
<head>
<meta charset="utf-8">
<title>RW Office Partners – Business Card</title>
<link href="https://fonts.googleapis.com/css2?family=Montserrat:wght@500;600;700&family=Arimo:wght@400&display=swap" rel="stylesheet">
<style>
  :root {
    --card-dark: #2a2a2b;
    --page: #3b3b3d;
    --brand-rose: #986474;
    --brand-slate: #7a8498;
    --white: #ffffff;
    --rule: #5a5a5c;
  }
  * { box-sizing: border-box; margin: 0; padding: 0; }
  html, body { width: 1200px; height: 1015px; overflow: hidden; }
  body {
    background: var(--page);
    display: flex;
    flex-direction: column;
    align-items: center;
    justify-content: center;
    gap: 56px;
  }
  .card {
    position: relative;
    width: 760px;
    height: 434px;
    background: var(--card-dark);
    overflow: hidden;
    box-shadow: 0 10px 28px rgba(0,0,0,.45);
  }
  .card__band {
    position: absolute;
    left: 0; right: 0; bottom: 0;
  }

  /* Front */
  .front .wordmark {
    position: absolute;
    top: 110px; left: 0; right: 0;
    text-align: center;
    font-family: "Montserrat", sans-serif;
    font-weight: 600;
    font-size: 46px;
    letter-spacing: 1px;
    color: var(--brand-rose);
  }
  .front .card__band {
    height: 148px;
    background: var(--brand-slate);
    display: flex;
    align-items: center;
    justify-content: center;
  }
  .tagline {
    font-family: "Montserrat", sans-serif;
    font-weight: 700;
    font-size: 17px;
    letter-spacing: .4px;
    text-transform: uppercase;
    color: var(--white);
  }

  /* Back */
  .back .wordmark {
    position: absolute;
    top: 150px; left: 40px;
    width: 300px;
    font-family: "Montserrat", sans-serif;
    font-weight: 600;
    font-size: 40px;
    line-height: 1.1;
    color: var(--brand-rose);
  }
  .back .divider {
    position: absolute;
    left: 362px; top: 90px;
    width: 1px; height: 160px;
    background: var(--rule);
  }
  .contacts {
    position: absolute;
    left: 392px; top: 92px;
    list-style: none;
    font-family: "Arimo", sans-serif;
    font-size: 18px;
  }
  .contacts li {
    display: flex;
    align-items: center;
    gap: 10px;
    height: 30px;
    color: var(--white);
  }
  .contacts li.contacts__web { color: var(--brand-rose); }
  .contacts svg { width: 20px; height: 20px; flex: none; }
  .back .card__band {
    height: 122px;
    background: var(--brand-rose);
  }
  .social {
    position: absolute;
    left: 360px; bottom: 150px;
    display: flex;
    align-items: center;
    gap: 10px;
    font-family: "Arimo", sans-serif;
    font-size: 20px;
    color: var(--white);
  }
  .social__dot {
    width: 26px; height: 26px;
    border: 2px solid var(--white);
    border-radius: 50%;
  }
</style>
</head>
<body>

  <section class="card front" aria-label="Card front">
    <div class="wordmark">RW Office Partners</div>
    <div class="card__band">
      <p class="tagline">Your organised problem solver</p>
    </div>
  </section>

  <section class="card back" aria-label="Card back">
    <div class="wordmark">RW Office Partners</div>
    <div class="divider"></div>
    <ul class="contacts">
      <li>
        <svg viewBox="0 0 20 20" fill="none" stroke="#986474" stroke-width="1.6">
          <rect x="2" y="2" width="16" height="16" rx="3"/>
          <path d="M7 5.5l1.6 2.6-1.1 1.1c.8 1.5 1.8 2.5 3.3 3.3l1.1-1.1 2.6 1.6-.9 1.7c-4 .2-7.9-3.7-7.6-7.7z"/>
        </svg>
        61 482 907 236
      </li>
      <li>
        <svg viewBox="0 0 20 20" fill="none" stroke="#986474" stroke-width="1.6">
          <rect x="2" y="4.5" width="16" height="11"/>
          <path d="M2 4.5l8 6 8-6"/>
        </svg>
        marisol@rwofficepartners.com.au
      </li>
      <li class="contacts__web">
        <svg viewBox="0 0 20 20" fill="none" stroke="#986474" stroke-width="1.5">
          <circle cx="10" cy="10" r="8"/>
          <ellipse cx="10" cy="10" rx="3.5" ry="8"/>
          <path d="M2 10h16M3.5 6h13M3.5 14h13"/>
        </svg>
        www.rwofficepartners.com.au
      </li>
    </ul>
    <div class="social">
      <span class="social__dot"></span>
      @rwofficepartners
    </div>
    <div class="card__band"></div>
  </section>

</body>
</html>
```